Hollow Thicket, a 3d voxel survival video game needs a card for gaming conventions

I am the lead developer for Hollow Thicket http://www.HollowThicket.example and need a business card to hand out at an indie gaming convention
The card would need to include the game name, website url, my name, position (Lead Developer), e-mail and phone number
The game is a 3d, voxel (with smooth terrain) based survival game with guns and wildlife. The main icon of the game would likely be a grizzly bear but I am willing to accept other designs too.
Attached is a media kit for the game with some images you can use but don't have to its just what little art I can provide. Anything on the website or from the video game can also be used. unrelated art can also be used.
Target Market(s)
Indie Developers/publishers at conferences
Industry/Entity Type
Games
Contact Information for Business Card
Name: Corin Waldrick
Position: Lead Developer
E-mail: Pale_Kettle@mailbox.example
Phone number: 555-372-1186

```html
<!DOCTYPE html>
<html lang="en">
<head>
<meta charset="utf-8">
<title>Hollow Thicket – Business Card</title>
<link href="https://fonts.googleapis.com/css2?family=Arimo:wght@400;700&display=swap" rel="stylesheet">
<style>
  :root {
    --page: #e9e6df;
    --card-light: #dcd2b4;
    --card-mid: #9a9272;
    --card-dark: #4a4630;
    --brand-red: #b3302a;
    --name-red: #c0282a;
    --title-white: #f7f4ea;
    --ink: #1e1c16;
    --bear-light: #b8764a;
    --bear-dark: #5e3418;
  }
  * { margin: 0; padding: 0; box-sizing: border-box; }
  html, body {
    width: 1200px; height: 892px; overflow: hidden;
    background: var(--page);
    font-family: "Arimo", Arial, sans-serif;
  }
  .canvas { position: relative; width: 1200px; height: 892px; }
  .card {
    position: absolute; left: 290px; width: 620px; height: 354px;
    overflow: hidden;
    background: radial-gradient(ellipse 75% 85% at 50% 58%, var(--card-light) 0%, var(--card-mid) 55%, var(--card-dark) 100%);
    box-shadow: 0 6px 18px rgba(0,0,0,0.18);
  }
  .card--front { top: 60px; }
  .card--back { top: 478px; }

  .brand {
    color: var(--brand-red);
    font-weight: 700;
    text-transform: uppercase;
    letter-spacing: 5px;
    line-height: 1;
  }
  .brand .line-1, .brand .line-2 { display: block; }
  .card--front .brand { position: absolute; left: 28px; top: 24px; font-size: 50px; }
  .card--front .brand .line-2 { padding-left: 50px; margin-top: 4px; }
  .card--back .brand { position: absolute; left: 150px; top: 104px; font-size: 62px; }
  .card--back .brand .line-2 { padding-left: 52px; margin-top: 6px; }

  .person { position: absolute; left: 32px; top: 162px; letter-spacing: 1.5px; }
  .person__name { color: var(--name-red); font-size: 16px; font-weight: 700; }
  .person__title { color: var(--title-white); font-size: 13px; font-weight: 700; margin-top: 3px; }

  .contact { position: absolute; left: 32px; top: 222px; list-style: none; }
  .contact__item {
    display: flex; align-items: center; gap: 8px;
    color: var(--ink); font-size: 15px; letter-spacing: 1px; margin-bottom: 9px;
  }
  .contact__icon { width: 16px; height: 16px; flex: none; }

  .mascot {
    position: absolute; left: 372px; top: 118px; width: 248px; height: 236px;
    background: radial-gradient(ellipse 48% 55% at 58% 48%, var(--bear-light) 0%, var(--bear-dark) 55%, rgba(94,52,24,0.35) 80%, rgba(94,52,24,0) 100%);
  }
</style>
</head>
<body>
<main class="canvas">
  <section class="card card--front">
    <div class="brand"><span class="line-1">Hollow</span><span class="line-2">Thicket</span></div>
    <div class="person">
      <p class="person__name">Corin Waldrick</p>
      <p class="person__title">Lead Developer</p>
    </div>
    <ul class="contact">
      <li class="contact__item">
        <svg class="contact__icon" viewBox="0 0 16 16" aria-hidden="true">
          <rect width="16" height="16" rx="2" fill="#f7f4ea"/>
          <path d="M5 3.5c-1 .6-1.3 1.8-.7 3.3.8 2 2.4 3.8 4.3 4.9 1.3.7 2.5.6 3.1-.3l-1.6-1.6-1.2.7c-1-.6-2-1.7-2.5-2.8l.8-1.1z" fill="#1e1c16"/>
        </svg>
        555-372-1186
      </li>
      <li class="contact__item">
        <svg class="contact__icon" viewBox="0 0 16 16" aria-hidden="true">
          <rect width="16" height="16" rx="2" fill="#f7f4ea"/>
          <rect x="3" y="5" width="10" height="7" fill="none" stroke="#1e1c16" stroke-width="1.2"/>
          <path d="M3 5l5 4 5-4" fill="none" stroke="#1e1c16" stroke-width="1.2"/>
        </svg>
        Pale_Kettle@mailbox.example
      </li>
      <li class="contact__item">
        <svg class="contact__icon" viewBox="0 0 16 16" aria-hidden="true">
          <rect width="16" height="16" rx="2" fill="#f7f4ea"/>
          <circle cx="8" cy="8" r="5" fill="none" stroke="#1e1c16" stroke-width="1.1"/>
          <ellipse cx="8" cy="8" rx="2.2" ry="5" fill="none" stroke="#1e1c16" stroke-width="1"/>
          <path d="M3 8h10" stroke="#1e1c16" stroke-width="1"/>
        </svg>
        www.HollowThicket.example
      </li>
    </ul>
    <div class="mascot" role="img" aria-label="Photograph of a roaring grizzly bear rising from the lower right corner"></div>
  </section>

  <section class="card card--back">
    <div class="brand"><span class="line-1">Hollow</span><span class="line-2">Thicket</span></div>
  </section>
</main>
</body>
</html>
```